Accommodation in an Executive Apartment for rent could be a Bed and breakfast,

Currently have a website and like the overall look but it needs revamping and want to add an instant booking button, which I would do later as the unit has a channel manager. Also want to be able to post blogs, etc. Need it to be viewed well on smart phones/tablets. all information related to this unit is on the current site which is www.hollowmerestays.com.au if you would view websites similar to roomvela.com and travonix.com Must be able to be coded in Wordpress

The current design is done in Wordpress so would want this functionality in any new design.

Target Market(s)

Workers at Parliamentary triangle, Canberra. Workers at Marlow centre Deakin, Workers at Westbrook Ellis Hanley Hospital, Workers at Fernvale Hospital, Public Servants Woden, Workers in Deakin ACT

Industry/Entity Type

Accommodation

Number of Pages Required

5+ page

Font styles to use
Sans Serif

Colors
ec1f27

Requirements
Must have
• Must have a classy look about it. Less clicks through the better. Not to wordy. Hard hitting points,
Nice to have
• Would like to retain the same colour theme and look
Should not have
• anything tacky

```html
<!DOCTYPE html>
<html lang="en">
<head>
<meta charset="utf-8">
<title>Hollowmere Stays</title>
<link href="https://fonts.googleapis.com/css2?family=Roboto:wght@300;400;500;700&display=swap" rel="stylesheet">
<style>
:root{
  --red:#ec1f27;
  --dark:#2b2b2b;
  --text:#555;
  --heading:#222;
  --line:#d6d6d6;
  --footer:#e9e9e9;
  --white:#fff;
}
*{margin:0;padding:0;box-sizing:border-box}
html,body{width:812px;height:1200px;overflow:hidden;background:var(--white)}
body{position:relative;font-family:'Roboto',Arial,sans-serif;color:var(--text)}
.abs{position:absolute}
.site-header{left:0;top:0;width:812px;height:66px;background:var(--red)}
.brand{left:52px;top:14px;font-size:28px;font-weight:400;color:var(--white);letter-spacing:.2px;line-height:36px}
.phone{left:624px;top:21px;display:flex;align-items:center;gap:9px;color:var(--white);font-size:19px;font-weight:500;letter-spacing:.5px}
.main-nav{left:0;top:66px;width:812px;height:33px;background:linear-gradient(#3a3a3a,#242424)}
.main-nav a{position:absolute;top:12px;font-size:8.5px;color:var(--white);text-decoration:none;letter-spacing:.3px}
.social{position:absolute;top:10px;width:13px;height:13px;border-radius:2px;background:var(--white)}
.hero{left:0;top:99px;width:812px;height:308px;background:linear-gradient(100deg,#6b5535 0%,#b08a52 35%,#d2ad72 60%,#a88658 100%)}
.booking{left:51px;top:162px;width:284px;height:184px;border:3px solid rgba(190,160,110,.75);background:rgba(70,55,35,.55)}
.booking h2{position:absolute;left:12px;top:14px;font-size:21px;font-weight:400;color:var(--white);letter-spacing:.5px}
.field{position:absolute;width:120px;height:23px;background:var(--white);font-size:7.5px;color:#444;padding:8px 7px 0}
.instant{position:absolute;left:12px;top:140px;width:253px;height:25px;background:var(--red);color:var(--white);font-size:14px;font-weight:500;text-align:center;line-height:25px;letter-spacing:.5px}
.dot{position:absolute;top:375px;width:7px;height:7px;border-radius:50%;background:var(--white)}
h3.section{position:absolute;font-size:18px;font-weight:400;color:var(--heading);letter-spacing:.4px}
.para{position:absolute;font-size:8.7px;line-height:16.3px;color:var(--text)}
.btn{position:absolute;width:84px;height:26px;background:var(--red);color:var(--white);font-size:7.5px;font-weight:500;text-align:center;line-height:26px;border-radius:2px}
.rule{position:absolute;left:51px;width:346px;height:1px;background:var(--line)}
.post-thumb{position:absolute;left:51px;width:102px;height:67px;background:linear-gradient(120deg,#8a6a3e,#d6b886 55%,#b49466)}
.post-title{position:absolute;left:165px;font-size:11.5px;color:var(--red)}
.post-text{position:absolute;left:165px;width:230px;font-size:8.5px;line-height:16px;color:var(--text)}
.post-meta{position:absolute;left:165px;font-size:7.5px;color:var(--red);display:flex;align-items:center;gap:4px}
.room{position:absolute;left:415px;width:347px;height:142px}
.room-bar{position:absolute;left:16px;top:85px;width:316px;height:45px;background:rgba(20,20,20,.8)}
.room-bar span{position:absolute;left:12px;top:11px;font-size:18px;font-weight:300;color:var(--white)}
.room-bar b{position:absolute;left:197px;top:7px;width:108px;height:31px;background:var(--red);color:var(--white);font-size:10px;font-weight:500;text-align:center;line-height:31px;letter-spacing:.3px}
.site-footer{left:0;top:1093px;width:812px;height:107px;background:var(--footer)}
.foot-nav a{position:absolute;top:27px;font-size:8px;color:#333;text-decoration:none;letter-spacing:.2px}
.copy{position:absolute;left:51px;font-size:7.8px;color:#555}
.news-title{position:absolute;left:578px;top:26px;font-size:11.5px;color:var(--heading);letter-spacing:.4px}
.news-input{position:absolute;left:579px;top:47px;width:153px;height:25px;background:var(--white);font-size:7.5px;color:#555;padding:9px 10px 0}
.news-btn{position:absolute;left:732px;top:47px;width:30px;height:25px;background:var(--red)}
</style>
</head>
<body>

<header class="abs site-header">
  <div class="abs brand">Hollowmere Stays</div>
  <div class="abs phone">
    <svg width="15" height="15" viewBox="0 0 15 15"><rect width="15" height="15" rx="3" fill="#fff"/><path d="M4.3 3.2l1.6-.3 1 2.3-1 .8c.6 1.3 1.5 2.2 2.8 2.8l.8-1 2.3 1-.3 1.6c-3.7.2-7.4-3.5-7.2-7.2z" fill="#ec1f27"/></svg>
    02 5550 1734
  </div>
</header>

<nav class="abs main-nav">
  <a style="left:50px">HOME</a>
  <a style="left:103px">B&amp;B ACCOMMODATION</a>
  <a style="left:227px">GALLERY</a>
  <a style="left:292px">WHAT'S NEARBY</a>
  <a style="left:388px">GUEST BOOK</a>
  <a style="left:470px">USEFUL LINKS</a>
  <a style="left:558px">CONTACT US</a>
  <span class="social" style="left:659px"></span>
  <span class="social" style="left:682px"></span>
  <span class="social" style="left:704px"></span>
  <span class="social" style="left:727px"></span>
  <span class="social" style="left:749px"></span>
</nav>

<section class="abs hero" role="img" aria-label="Photo of the apartment living room with television unit and glass dining table"></section>

<form class="abs booking">
  <h2>QUICK BOOKING</h2>
  <div class="field" style="left:12px;top:49px">Name</div>
  <div class="field" style="left:144px;top:49px">Email Address</div>
  <div class="field" style="left:12px;top:78px">Phone No.</div>
  <div class="field" style="left:144px;top:78px">No of Bedroom</div>
  <div class="field" style="left:12px;top:107px">Select Date</div>
  <div class="field" style="left:144px;top:107px">No of People</div>
  <div class="instant">INSTANT BOOKING</div>
</form>

<span class="dot" style="left:384px;background:var(--red)"></span>
<span class="dot" style="left:396px"></span>
<span class="dot" style="left:409px"></span>
<span class="dot" style="left:422px"></span>

<h3 class="section" style="left:51px;top:437px">WELCOME TO OUR WEBSITE</h3>
<p class="para" style="left:51px;top:468px;width:348px">Aliquam molestie, mi et imperdiet euismod, dui purus auctor tellus, et interdum lacus lectus et ante. Sed accumsan sollicitudin sapien, sit amet adipiscing turpis gravida ac. In congue, neque ac lobortis volutpat, libero mauris varius mi, vitae suscipit ipsum ligula vitae risus. Duis aliquam nibh a dui iaculis viverra id a velit. Vivamus egestas risus in magna varius commodo.</p>
<div class="btn" style="left:51px;top:567px">READ MORE</div>
<div class="rule" style="top:614px"></div>

<h3 class="section" style="left:51px;top:628px">WHY CHOOSE US?</h3>
<p class="para" style="left:51px;top:655px;width:348px">Aliquam molestie, mi et imperdiet euismod, dui purus auctor tellus, et interdum lacus lectus et ante. Sed accumsan sollicitudin sapien, sit amet adipiscing turpis gravida ac. In congue, neque ac lobortis volutpat, libero mauris varius mi, vitae suscipit ipsum ligula vitae risus.</p>
<div class="btn" style="left:51px;top:729px">READ MORE</div>
<div class="rule" style="top:772px"></div>

<h3 class="section" style="left:51px;top:786px">BLOG POSTS</h3>

<div class="post-thumb" style="top:819px" role="img" aria-label="Photo of the open-plan living area"></div>
<div class="post-title" style="top:817px">Sed accumsan sollicitudin sapien...</div>
<p class="post-text" style="top:834px">Sit amet adipiscing turpis gravida ac. In congue, neque ac lobortis volutpat, libero mauris varius mi..</p>
<div class="post-meta" style="top:876px"><svg width="8" height="8" viewBox="0 0 8 8"><rect x=".5" y="1.5" width="7" height="6" fill="none" stroke="#ec1f27"/><rect x=".5" y="1.5" width="7" height="2" fill="#ec1f27"/></svg>Nov 15, 2015 &nbsp;|&nbsp; <svg width="7" height="8" viewBox="0 0 7 8"><circle cx="3.5" cy="2" r="2" fill="#ec1f27"/><path d="M0 8c0-3 7-3 7 0z" fill="#ec1f27"/></svg>Admin</div>

<div class="post-thumb" style="top:909px;background:linear-gradient(120deg,#c9bfae,#f0ebe2 55%,#9f8a6c)" role="img" aria-label="Photo of the laundry with washing machine"></div>
<div class="post-title" style="top:907px">Sed accumsan sollicitudin sapien...</div>
<p class="post-text" style="top:924px">Sit amet adipiscing turpis gravida ac. In congue, neque ac lobortis volutpat, libero mauris varius mi..</p>
<div class="post-meta" style="top:966px"><svg width="8" height="8" viewBox="0 0 8 8"><rect x=".5" y="1.5" width="7" height="6" fill="none" stroke="#ec1f27"/><rect x=".5" y="1.5" width="7" height="2" fill="#ec1f27"/></svg>Nov 15, 2015 &nbsp;|&nbsp; <svg width="7" height="8" viewBox="0 0 7 8"><circle cx="3.5" cy="2" r="2" fill="#ec1f27"/><path d="M0 8c0-3 7-3 7 0z" fill="#ec1f27"/></svg>Admin</div>

<div class="post-thumb" style="top:1000px;background:linear-gradient(120deg,#6e5438,#c6a77c 55%,#8c6f4c)" role="img" aria-label="Photo of the lounge with armchairs"></div>
<div class="post-title" style="top:998px">Sed accumsan sollicitudin sapien...</div>
<p class="post-text" style="top:1015px">Sit amet adipiscing turpis gravida ac. In congue, neque ac lobortis volutpat, libero mauris varius mi..</p>
<div class="post-meta" style="top:1057px"><svg width="8" height="8" viewBox="0 0 8 8"><rect x=".5" y="1.5" width="7" height="6" fill="none" stroke="#ec1f27"/><rect x=".5" y="1.5" width="7" height="2" fill="#ec1f27"/></svg>Nov 15, 2015 &nbsp;|&nbsp; <svg width="7" height="8" viewBox="0 0 7 8"><circle cx="3.5" cy="2" r="2" fill="#ec1f27"/><path d="M0 8c0-3 7-3 7 0z" fill="#ec1f27"/></svg>Admin</div>

<h3 class="section" style="left:415px;top:437px">B&amp;B ACCOMMODATION</h3>

<div class="room" style="top:473px;background:linear-gradient(110deg,#6a4a2c,#b58c5c 45%,#d9c3a0 80%,#9c8266)" role="img" aria-label="Photo of the lounge room">
  <div class="room-bar"><span>Vivamus egestas risus</span><b>INSTANT BOOKING</b></div>
</div>
<div class="room" style="top:622px;background:linear-gradient(110deg,#8f7f68,#d8cdb8 45%,#eee6d6 70%,#a59276)" role="img" aria-label="Photo of the dining area by the window">
  <div class="room-bar"><span>Vivamus egestas risus</span><b>INSTANT BOOKING</b></div>
</div>
<div class="room" style="top:773px;background:linear-gradient(110deg,#a89a86,#5e4a3a 40%,#6d7a4a 70%,#3f5a2e)" role="img" aria-label="Photo of the outdoor courtyard with garden">
  <div class="room-bar"><span>Vivamus egestas risus</span><b>INSTANT BOOKING</b></div>
</div>
<div class="room" style="top:923px;background:linear-gradient(110deg,#3e3a36,#8f877c 45%,#b7ada0 70%,#6e5c4c)" role="img" aria-label="Photo of the table set with wine and glasses">
  <div class="room-bar"><span>Vivamus egestas risus</span><b>INSTANT BOOKING</b></div>
</div>

<footer class="abs site-footer">
  <nav class="foot-nav">
    <a style="left:51px">HOME</a>
    <a style="left:91px">B&amp;B ACCOMMODATION</a>
    <a style="left:197px">GALLERY</a>
    <a style="left:248px">WHAT'S NEARBY</a>
    <a style="left:329px">GUEST BOOK</a>
    <a style="left:396px">USEFUL LINKS</a>
    <a style="left:469px">CONTACT US</a>
  </nav>
  <p class="copy" style="top:58px">Copyright © 2015. Company Name.All Right Reserved</p>
  <p class="copy" style="top:72px">Terms of Services &nbsp;|&nbsp; Privacy Policy</p>
  <div class="news-title">NEWSLETTER SIGN UP</div>
  <div class="news-input">Enter Email Address</div>
  <div class="news-btn"><svg width="30" height="25" viewBox="0 0 30 25"><path d="M13 7.5l5 5-5 5" fill="none" stroke="#fff" stroke-width="2.5"/></svg></div>
</footer>

</body>
</html>
```